Pitch Deck Redesign

We are a company in the ed-tech/gaming business wishing to fine-tune the looks of our pitch deck/company presentation.
Attached is the current template we use. And while we want to keep the headlines, general structure and the flow represented in various graphs, we want a design whizz to fine-tune the looks of it, updating graphics and add a bit more graphics. In the end we basically want to give the template a professional edge while still conveying the design philosophy we're trying to achieve, the philosophy is as follows:
A combination of education and playfulness/digital entertainment (particularly gaming). It should additionally be clean, not cluttered yet with a hint of fun.
We of course want to be able to simply ad our own texts as well as our to logo various elements

```html
<!DOCTYPE html>
<html lang="en">
<head>
<meta charset="utf-8">
<title>Pitch Deck Slides</title>
<link href="https://fonts.googleapis.com/css2?family=Open+Sans:wght@400;600;700&display=swap" rel="stylesheet">
<style>
:root{
  --blue:#0b4fb3;
  --blue-deep:#0a3a8f;
  --blue-bright:#1467cf;
  --orange:#f7821b;
  --ink:#2b2b2b;
  --white:#ffffff;
  --slate:#4f6478;
  --teal:#16808a;
}
*{margin:0;padding:0;box-sizing:border-box}
html,body{width:1200px;height:719px;overflow:hidden;background:var(--white)}
body{font-family:"Open Sans",Arial,sans-serif;color:var(--ink)}
.sheet{position:relative;width:1200px;height:719px;background:var(--white)}
.slide{position:absolute;width:380px;height:214px;background:var(--white);overflow:hidden;box-shadow:0 2px 6px rgba(0,0,0,.28)}
.slide.col-1{left:15px}.slide.col-2{left:409px}.slide.col-3{left:805px}
.slide.row-1{top:21px}.slide.row-2{top:256px}.slide.row-3{top:483px}
.slide.is-dark{background:linear-gradient(120deg,var(--blue-deep) 0%,var(--blue) 45%,var(--blue-deep) 100%)}
.slide-header{position:absolute;left:0;top:0;width:100%;height:39px;background:linear-gradient(90deg,var(--blue) 0%,#0d58c0 55%,var(--blue-deep) 100%)}
.slide-footer{position:absolute;left:0;bottom:0;width:100%;height:17px;background:linear-gradient(90deg,var(--blue) 0%,#0d58c0 55%,var(--blue-deep) 100%);color:var(--white);font-size:7px;line-height:17px;padding:0 18px}
.slide-footer .page-no{position:absolute;right:18px;top:0}
.brand{position:absolute;left:18px;top:7px;color:var(--white);font-weight:600;font-size:19px;letter-spacing:.2px}
.section-title{position:absolute;left:18px;top:58px;color:var(--orange);font-weight:600;font-size:10px;letter-spacing:.1px}
.body-copy{position:absolute;font-size:4.6px;line-height:6.8px;color:var(--ink);text-align:justify}
.body-copy p+p{margin-top:6px}
.bullets{position:absolute;list-style:none;font-size:4.6px;line-height:6.8px;color:var(--ink)}
.bullets li{position:relative;padding-left:10px;margin-bottom:6px}
.bullets li::before{content:"";position:absolute;left:0;top:1.4px;width:3.2px;height:3.2px;border-radius:50%;background:var(--blue);box-shadow:0 0 0 .8px var(--white),0 0 0 1.4px var(--blue)}
.art{position:absolute;left:0;top:0}
/* cover & contact */
.cover-brand{position:absolute;left:17px;top:20px;color:var(--white);font-weight:600;font-size:19px}
.cover-tagline{position:absolute;left:19px;top:42px;color:var(--white);font-size:9.5px}
.cover-title{position:absolute;left:18px;top:83px;font-weight:700;font-size:17.5px;line-height:24px;color:var(--white)}
.cover-title .accent{color:var(--orange)}
.url-pill{position:absolute;left:13px;top:148px;width:116px;height:13px;background:var(--orange);clip-path:polygon(5px 0,calc(100% - 5px) 0,100% 50%,calc(100% - 5px) 100%,5px 100%,0 50%);color:var(--white);font-weight:700;font-size:9.5px;line-height:13px;text-align:center}
.contact-title{position:absolute;left:18px;top:84px;color:var(--orange);font-weight:700;font-size:17.5px}
.contact-list{position:absolute;left:18px;top:114px;list-style:none;color:var(--white);font-size:8.5px}
.contact-list li{display:flex;align-items:center;height:15.3px}
.contact-list svg{width:9px;height:9px;margin-right:7px}
/* why we exist */
.quote-text{position:absolute;left:22px;top:119px;width:90px;color:var(--white);font-size:8px;line-height:11.5px}
.stat-band{position:absolute;left:129px;top:152px;width:251px;height:39px;background:var(--orange);display:flex;justify-content:space-around;align-items:center;padding:0 4px}
.stat-band .stat{text-align:center}
.stat-band .stat-value{color:var(--blue);font-weight:700;font-size:12px;line-height:14px}
.stat-band .stat-label{color:var(--white);font-size:8px;line-height:11px}
.stat-grid{position:absolute;left:185px;top:81px;width:172px;height:81px;display:grid;grid-template-columns:1fr 1fr;grid-template-rows:1fr 1fr}
.stat-grid .stat{text-align:center;padding-top:3px}
.stat-grid .stat-value{color:var(--blue);font-weight:700;font-size:12px;line-height:14px}
.stat-grid .stat-label{color:var(--orange);font-size:8.5px;line-height:11px}
.stat-grid .divider-v{position:absolute;left:80px;top:0;width:.7px;height:81px;background:#8ea7d8}
.stat-grid .divider-h{position:absolute;left:0;top:37px;width:172px;height:.7px;background:#8ea7d8}
/* network labels */
.node-label{position:absolute;font-size:5.5px;color:var(--ink);transform:translateX(-50%);white-space:nowrap}
.node-label.tiny{font-size:3.8px}
.app-note{position:absolute;width:64px;font-size:4.6px;line-height:6.8px;color:var(--ink)}
.app-note.right{text-align:right}
</style>
</head>
<body>
<svg width="0" height="0" style="position:absolute">
  <defs>
    <symbol id="icon-doc" viewBox="-6 -7 12 14">
      <path d="M-4.5 -6H2L4.5 -3.5V6H-4.5Z" fill="none" stroke="#fff" stroke-width="1"/>
      <path d="M-2.5 -2H2.5M-2.5 0H2.5M-2.5 2H2.5M-2.5 4H1" stroke="#fff" stroke-width=".8"/>
    </symbol>
    <symbol id="icon-pen" viewBox="-6 -7 12 14">
      <path d="M0 -3L3.5 1L0 5.5L-3.5 1Z" fill="none" stroke="#fff" stroke-width="1"/>
      <circle cx="0" cy="1" r=".9" fill="#fff"/>
      <path d="M-5 -4H5M0 -6V-3" stroke="#fff" stroke-width=".9"/>
    </symbol>
  </defs>
</svg>

<main class="sheet">

  <!-- Cover -->
  <section class="slide is-dark col-1 row-1">
    <svg class="art" width="380" height="214" role="img" aria-label="Photo of two colleagues working at a computer">
      <defs><linearGradient id="photo-cover" x1="0" y1="0" x2="1" y2="1"><stop offset="0" stop-color="#e8d9c2"/><stop offset=".55" stop-color="#9fb2c4"/><stop offset="1" stop-color="#4a5f74"/></linearGradient></defs>
      <polygon transform="translate(273 109)" points="96,0 48,83 -48,83 -96,0 -48,-83 48,-83" fill="var(--orange)"/>
      <polygon transform="translate(273 109)" points="0,-100 86.6,-50 86.6,50 0,100 -86.6,50 -86.6,-50" fill="url(#photo-cover)" stroke="#fff" stroke-width="1.5"/>
    </svg>
    <div class="cover-brand">LOGO HERE</div>
    <div class="cover-tagline">Tagline Here</div>
    <h1 class="cover-title"><span class="accent">PRESENTATION</span><br>TITLE GOES HERE</h1>
    <div class="url-pill">www.brightquest.com</div>
  </section>

  <!-- Mission -->
  <section class="slide col-2 row-1">
    <header class="slide-header"><div class="brand">LOGO HERE</div></header>
    <h2 class="section-title">MISSION STATEMENT AND VISION</h2>
    <div class="body-copy" style="left:18px;top:84px;width:163px">
      <p>Lorem ipsum dolor sit amet, consectetur adipiscing elit, sed do eiusmod tempor incididunt ut labore et dolore magna aliqua. Pharetra sit amet aliquam id diam maecenas ultricies. Volutpat maecenas volutpat Eget egestas purus viverra accumsan. Luctus accumsan tortor posuere ac ut consequat semper. Odio morbi quis commodo odio. Viverra justo nec ultrices dui sapien.</p>
      <p>Convallis convallis tellus id interdum velit laoreet. Egestas quis ipsum suspendisse ultrices. Dictumst quisque sagittis purus sit amet volutpat consequat. Mauris augue neque gravida in fermentum etc.</p>
    </div>
    <svg class="art" width="380" height="214" role="img" aria-label="Photo of a person overlooking a city skyline at dusk">
      <defs><linearGradient id="photo-city" x1="0" y1="0" x2="0" y2="1"><stop offset="0" stop-color="#8aa0c8"/><stop offset=".35" stop-color="#c79aa6"/><stop offset=".55" stop-color="#2a3f6e"/><stop offset="1" stop-color="#0f2048"/></linearGradient></defs>
      <polygon transform="translate(290 115)" points="78,0 39,67.5 -39,67.5 -78,0 -39,-67.5 39,-67.5" fill="var(--orange)"/>
      <polygon transform="translate(290 115)" points="0,-79 68.4,-39.5 68.4,39.5 0,79 -68.4,39.5 -68.4,-39.5" fill="url(#photo-city)" stroke="#fff" stroke-width="1.2"/>
    </svg>
    <footer class="slide-footer">WWW.BRIGHTQUEST.COM<span class="page-no">1</span></footer>
  </section>

  <!-- Story -->
  <section class="slide col-3 row-1">
    <header class="slide-header"><div class="brand">LOGO HERE</div></header>
    <h2 class="section-title" style="top:57px">STORY</h2>
    <div class="body-copy" style="left:18px;top:84px;width:160px">
      <p>Lorem ipsum dolor sit amet, consectetur adipiscing elit, sed do eiusmod tempor incididunt ut labore et dolore magna aliqua. Pharetra sit amet aliquam id diam maecenas ultricies. Volutpat maecenas volutpat Eget egestas purus viverra accumsan. Luctus accumsan tortor posuere ac ut consequat semper. Odio morbi quis commodo odio. Viverra justo nec ultrices dui sapien.</p>
      <p>Convallis convallis tellus id interdum velit laoreet. Egestas quis ipsum suspendisse ultrices. Dictumst quisque sagittis purus sit amet volutpat consequat. Mauris augue neque gravida in fermentum et</p>
    </div>
    <div class="body-copy" style="left:190px;top:84px;width:160px">
      <p>Lorem ipsum dolor sit amet, consectetur adipiscing elit, sed do eiusmod tempor incididunt ut labore et dolore magna aliqua. Pharetra sit amet aliquam id diam maecenas ultricies. Volutpat maecenas volutpat Eget egestas purus viverra accumsan. Luctus accumsan tortor posuere ac ut consequat semper. Odio morbi quis commodo odio. Viverra justo nec ultrices dui sapien.</p>
      <p>Convallis convallis tellus id interdum velit laoreet. Egestas quis ipsum suspendisse ultrices. Dictumst quisque sagittis purus sit amet volutpat consequat. Mauris augue neque gravida in fermentum et</p>
    </div>
    <footer class="slide-footer">WWW.BRIGHTQUEST.COM<span class="page-no">2</span></footer>
  </section>

  <!-- Why we exist A -->
  <section class="slide col-1 row-2">
    <header class="slide-header"><div class="brand">LOGO HERE</div></header>
    <h2 class="section-title">WHY WE EXIST</h2>
    <svg class="art" width="380" height="214" aria-hidden="true">
      <polygon transform="translate(62 135)" points="55,0 27.5,47.6 -27.5,47.6 -55,0 -27.5,-47.6 27.5,-47.6" fill="var(--orange)"/>
      <polygon transform="translate(62 135)" points="0,-56 48.5,-28 48.5,28 0,56 -48.5,28 -48.5,-28" fill="var(--blue)"/>
    </svg>
    <p class="quote-text">Lorem ipsum dolor sit amet, consectetur adipiscing elit <b style="font-size:10px">”</b></p>
    <ul class="bullets" style="left:137px;top:91px;width:236px">
      <li>Lorem ipsum dolor sit amet, consectetur adipiscing elit, sed do eiusmod tempor incididunt ut labore et dolore magna aliqua. Pharetra sit amet aliquam id diam Maecenas</li>
      <li>Eget egestas purus viverra accumsan. Luctus accumsan tortor posuere ac ut consequat semper.</li>
      <li>Convallis convallis tellus id interdum velit laoreet. Egestas quis ipsum suspendisse ultrices.</li>
    </ul>
    <div class="stat-band">
      <div class="stat"><div class="stat-value">2,8 BILLION</div><div class="stat-label">Stat description</div></div>
      <div class="stat"><div class="stat-value">9 of 10</div><div class="stat-label">Stat description</div></div>
      <div class="stat"><div class="stat-value">90%</div><div class="stat-label">Stat description</div></div>
    </div>
    <footer class="slide-footer">WWW.BRIGHTQUEST.COM<span class="page-no">3</span></footer>
  </section>

  <!-- Why we exist B -->
  <section class="slide col-2 row-2">
    <header class="slide-header"><div class="brand">LOGO HERE</div></header>
    <h2 class="section-title">WHY WE EXIST</h2>
    <ul class="bullets" style="left:18px;top:85px;width:136px">
      <li>Lorem ipsum dolor sit amet, consectetur adipiscing elit, sed do eiusmod tempor incididunt ut labore et dolore magna aliqua. Pharetra sit amet aliquam id diam Maecenas</li>
      <li>Eget egestas purus viverra accumsan. Luctus accumsan tortor posuere ac ut consequat semper.</li>
      <li>Convallis convallis tellus id interdum velit laoreet. Egestas quis ipsum suspendisse ultrices.</li>
    </ul>
    <div class="stat-grid">
      <div class="stat"><div class="stat-value">15,7%</div><div class="stat-label">Stat description</div></div>
      <div class="stat"><div class="stat-value">43%</div><div class="stat-label">Stat description</div></div>
      <div class="stat" style="padding-top:6px"><div class="stat-value">30%</div><div class="stat-label">Stat description</div></div>
      <div class="stat" style="padding-top:6px"><div class="stat-value">1 of 5</div><div class="stat-label">Stat description</div></div>
      <span class="divider-v"></span><span class="divider-h"></span>
    </div>
    <footer class="slide-footer">WWW.BRIGHTQUEST.COM<span class="page-no">4</span></footer>
  </section>

  <!-- Solution -->
  <section class="slide col-3 row-2">
    <header class="slide-header"><div class="brand">LOGO HERE</div></header>
    <h2 class="section-title">OUR SOLUTION</h2>
    <ul class="bullets" style="left:18px;top:85px;width:136px;text-align:justify">
      <li>Lorem ipsum dolor sit amet, consectetur adipiscing elit, sed do eiusmod tempor incididunt ut labore et dolore magna aliqua. Pharetra sit amet aliquam id diam maecenas ultricies. Volutpat maecenas volutpat</li>
      <li>Eget egestas purus viverra accumsan. Luctus accumsan tortor posuere ac ut consequat semper. Odio morbi quis commodo odio. Viverra justo nec ultrices dui sapien.</li>
      <li>Convallis convallis tellus id interdum velit laoreet. Egestas quis ipsum suspendisse ultrices. Dictumst quisque sagittis purus sit amet volutpat consequat. Mauris augue neque gravida in fermentum et</li>
    </ul>
    <svg class="art" width="380" height="214" aria-hidden="true">
      <g stroke="var(--blue)" stroke-width=".7" stroke-dasharray="2 1.5" fill="none">
        <path d="M189 102L271 119L347 102M271 119V169"/>
      </g>
      <g fill="var(--blue)" stroke="var(--orange)" stroke-width="1.2">
        <polygon transform="translate(189 102)" points="0,-17 14.7,-8.5 14.7,8.5 0,17 -14.7,8.5 -14.7,-8.5"/>
        <polygon transform="translate(347 102)" points="0,-17 14.7,-8.5 14.7,8.5 0,17 -14.7,8.5 -14.7,-8.5"/>
        <polygon transform="translate(271 119)" points="0,-17 14.7,-8.5 14.7,8.5 0,17 -14.7,8.5 -14.7,-8.5"/>
        <polygon transform="translate(272 169)" points="0,-17 14.7,-8.5 14.7,8.5 0,17 -14.7,8.5 -14.7,-8.5"/>
      </g>
      <use href="#icon-doc" x="182" y="94" width="14" height="16"/>
      <use href="#icon-doc" x="340" y="94" width="14" height="16"/>
      <use href="#icon-pen" x="265" y="161" width="14" height="16"/>
      <text x="271" y="122" fill="#fff" font-size="7" font-weight="600" text-anchor="middle" font-family="Open Sans, sans-serif">LOGO</text>
    </svg>
    <span class="node-label" style="left:189px;top:126px">Description</span>
    <span class="node-label" style="left:347px;top:126px">Description</span>
    <span class="node-label" style="left:272px;top:189px">Graphic</span>
    <footer class="slide-footer">WWW.BRIGHTQUEST.COM<span class="page-no">5</span></footer>
  </section>

  <!-- Ecosystem -->
  <section class="slide col-1 row-3">
    <header class="slide-header"><div class="brand">LOGO HERE</div></header>
    <h2 class="section-title" style="top:55px">OUR ECOSYSTEM</h2>
    <svg class="art" width="380" height="214" aria-hidden="true">
      <g stroke="var(--blue)" stroke-width=".6" stroke-dasharray="1.5 1.2" fill="none">
        <path d="M78 87L136 106L186 121L236 106L312 89"/>
        <path d="M78 176L136 151L186 121L236 151L314 176"/>
        <path d="M314 176H78"/>
      </g>
      <g fill="var(--orange)">
        <polygon transform="translate(78 87)" points="0,-12 10.4,-6 10.4,6 0,12 -10.4,6 -10.4,-6"/>
        <polygon transform="translate(136 106)" points="0,-12 10.4,-6 10.4,6 0,12 -10.4,6 -10.4,-6"/>
        <polygon transform="translate(236 106)" points="0,-12 10.4,-6 10.4,6 0,12 -10.4,6 -10.4,-6"/>
        <polygon transform="translate(312 89)" points="0,-12 10.4,-6 10.4,6 0,12 -10.4,6 -10.4,-6"/>
        <polygon transform="translate(136 151)" points="0,-12 10.4,-6 10.4,6 0,12 -10.4,6 -10.4,-6"/>
        <polygon transform="translate(236 151)" points="0,-12 10.4,-6 10.4,6 0,12 -10.4,6 -10.4,-6"/>
        <polygon transform="translate(78 176)" points="0,-12 10.4,-6 10.4,6 0,12 -10.4,6 -10.4,-6"/>
        <polygon transform="translate(187 176)" points="0,-12 10.4,-6 10.4,6 0,12 -10.4,6 -10.4,-6"/>
        <polygon transform="translate(314 176)" points="0,-12 10.4,-6 10.4,6 0,12 -10.4,6 -10.4,-6"/>
      </g>
      <polygon transform="translate(78 87)" points="0,-10.5 9.1,-5.3 9.1,5.3 0,10.5 -9.1,5.3 -9.1,-5.3" fill="var(--slate)"/>
      <polygon transform="translate(136 106)" points="0,-10.5 9.1,-5.3 9.1,5.3 0,10.5 -9.1,5.3 -9.1,-5.3" fill="#5c7b9b"/>
      <polygon transform="translate(236 106)" points="0,-10.5 9.1,-5.3 9.1,5.3 0,10.5 -9.1,5.3 -9.1,-5.3" fill="var(--teal)"/>
      <polygon transform="translate(312 89)" points="0,-10.5 9.1,-5.3 9.1,5.3 0,10.5 -9.1,5.3 -9.1,-5.3" fill="var(--blue)"/>
      <polygon transform="translate(136 151)" points="0,-10.5 9.1,-5.3 9.1,5.3 0,10.5 -9.1,5.3 -9.1,-5.3" fill="#4f7f87"/>
      <polygon transform="translate(236 151)" points="0,-10.5 9.1,-5.3 9.1,5.3 0,10.5 -9.1,5.3 -9.1,-5.3" fill="var(--teal)"/>
      <polygon transform="translate(78 176)" points="0,-10.5 9.1,-5.3 9.1,5.3 0,10.5 -9.1,5.3 -9.1,-5.3" fill="#3f5a55"/>
      <polygon transform="translate(187 176)" points="0,-10.5 9.1,-5.3 9.1,5.3 0,10.5 -9.1,5.3 -9.1,-5.3" fill="var(--slate)"/>
      <polygon transform="translate(314 176)" points="0,-10.5 9.1,-5.3 9.1,5.3 0,10.5 -9.1,5.3 -9.1,-5.3" fill="#1f7fa0"/>
      <polygon transform="translate(186 121)" points="0,-16 13.9,-8 13.9,8 0,16 -13.9,8 -13.9,-8" fill="var(--blue)"/>
      <text x="186" y="124" fill="#fff" font-size="6.5" font-weight="600" text-anchor="middle" font-family="Open Sans, sans-serif">LOGO</text>
      <g>
        <use href="#icon-doc" x="73" y="81" width="10" height="12"/>
        <use href="#icon-doc" x="131" y="100" width="10" height="12"/>
        <use href="#icon-doc" x="231" y="100" width="10" height="12"/>
        <use href="#icon-doc" x="307" y="83" width="10" height="12"/>
        <use href="#icon-doc" x="131" y="145" width="10" height="12"/>
        <use href="#icon-doc" x="231" y="145" width="10" height="12"/>
        <use href="#icon-doc" x="73" y="170" width="10" height="12"/>
        <use href="#icon-doc" x="182" y="170" width="10" height="12"/>
        <use href="#icon-doc" x="309" y="170" width="10" height="12"/>
      </g>
    </svg>
    <span class="node-label tiny" style="left:78px;top:104px">Description</span>
    <span class="node-label tiny" style="left:136px;top:123px">Description</span>
    <span class="node-label tiny" style="left:236px;top:123px">Description</span>
    <span class="node-label tiny" style="left:312px;top:106px">Description</span>
    <span class="node-label tiny" style="left:140px;top:167px">Description</span>
    <span class="node-label tiny" style="left:236px;top:167px">Description</span>
    <span class="node-label tiny" style="left:79px;top:191px">Description</span>
    <span class="node-label tiny" style="left:188px;top:191px">Description</span>
    <span class="node-label tiny" style="left:317px;top:190px">Description</span>
    <footer class="slide-footer">WWW.BRIGHTQUEST.COM<span class="page-no">6</span></footer>
  </section>

  <!-- The app -->
  <section class="slide col-2 row-3">
    <header class="slide-header"><div class="brand">LOGO HERE</div></header>
    <h2 class="section-title" style="top:55px">THE APP</h2>
    <svg class="art" width="380" height="214" aria-hidden="true">
      <g stroke="var(--blue)" stroke-width=".6" fill="none">
        <path d="M89 76H129L150 96"/>
        <path d="M89 118H160"/>
        <path d="M89 155H129L150 135"/>
        <path d="M291 76H250L229 96"/>
        <path d="M291 118H220"/>
        <path d="M291 155H250L229 135"/>
      </g>
      <g fill="#fff" stroke="var(--blue)" stroke-width=".8">
        <circle cx="89" cy="76" r="1.8"/><circle cx="89" cy="118" r="1.8"/><circle cx="89" cy="155" r="1.8"/>
        <circle cx="291" cy="76" r="1.8"/><circle cx="291" cy="118" r="1.8"/><circle cx="291" cy="155" r="1.8"/>
      </g>
      <circle cx="189" cy="132" r="52" fill="var(--orange)"/>
      <defs><linearGradient id="app-screen" x1="0" y1="0" x2="0" y2="1"><stop offset="0" stop-color="#1aa0ee"/><stop offset="1" stop-color="#0a63c9"/></linearGradient></defs>
      <rect x="161" y="76" width="55" height="107" rx="7" fill="#1b1b1f"/>
      <rect x="163.5" y="78.5" width="50" height="102" rx="5.5" fill="url(#app-screen)"/>
      <rect x="178" y="78.5" width="21" height="3.5" rx="1.7" fill="#1b1b1f"/>
      <text x="188.5" y="134" fill="#fff" font-size="10.5" font-weight="700" text-anchor="middle" font-family="Open Sans, sans-serif">OUR APP</text>
    </svg>
    <p class="app-note" style="left:18px;top:74px">Eget egestas purus viverra accumsan. Luctus accumsan tortor posuere</p>
    <p class="app-note" style="left:18px;top:112px">Eget egestas purus viverra accumsan. Luctus accumsan tortor posuere</p>
    <p class="app-note" style="left:18px;top:149px">Eget egestas purus viverra accumsan. Luctus accumsan tortor posuere</p>
    <p class="app-note right" style="left:297px;top:74px">Eget egestas purus viverra accumsan. Luctus accumsan tortor posuere</p>
    <p class="app-note right" style="left:297px;top:112px">Eget egestas purus viverra accumsan. Luctus accumsan tortor posuere</p>
    <p class="app-note right" style="left:297px;top:149px">Eget egestas purus viverra accumsan. Luctus accumsan tortor posuere</p>
    <footer class="slide-footer">WWW.BRIGHTQUEST.COM<span class="page-no">7</span></footer>
  </section>

  <!-- Contact -->
  <section class="slide is-dark col-3 row-3">
    <svg class="art" width="380" height="214" role="img" aria-label="Photo of hands typing on a laptop keyboard">
      <defs><linearGradient id="photo-laptop" x1="0" y1="0" x2="1" y2="1"><stop offset="0" stop-color="#f3e6cf"/><stop offset=".5" stop-color="#e6c8ab"/><stop offset="1" stop-color="#9c9fa6"/></linearGradient></defs>
      <polygon transform="translate(273 109)" points="96,0 48,83 -48,83 -96,0 -48,-83 48,-83" fill="var(--orange)"/>
      <polygon transform="translate(273 109)" points="0,-100 86.6,-50 86.6,50 0,100 -86.6,50 -86.6,-50" fill="url(#photo-laptop)" stroke="#fff" stroke-width="1.5"/>
    </svg>
    <div class="cover-brand">LOGO HERE</div>
    <div class="cover-tagline">Tagline Here</div>
    <h2 class="contact-title">CONTACT US</h2>
    <ul class="contact-list">
      <li><svg viewBox="0 0 10 10"><path d="M2 .8L3.6 .6L4.5 2.8L3.4 3.7Q4.3 5.6 6.3 6.6L7.2 5.5L9.4 6.4L9.2 8Q8.8 9.3 7.4 9.2Q1 8.2 .8 2.6Q.7 1.2 2 .8Z" fill="#fff"/></svg>123-456-7890</li>
      <li><svg viewBox="0 0 10 10"><rect x=".5" y="2" width="9" height="6.5" fill="#fff"/><path d="M.8 2.3L5 5.6L9.2 2.3" stroke="var(--blue)" stroke-width=".9" fill="none"/></svg>hello@brightquest.com</li>
      <li><svg viewBox="0 0 10 10"><g stroke="#fff" stroke-width=".8" fill="none"><circle cx="5" cy="5" r="4.2"/><ellipse cx="5" cy="5" rx="1.8" ry="4.2"/><path d="M.8 5H9.2M1.5 3H8.5M1.5 7H8.5"/></g></svg>www.brightquest.com</li>
    </ul>
  </section>

</main>
</body>
</html>
```